Business Card for Coastal Tundrabridge Advisory

We need a business card for Coastal Tundrabridge Advisory. The company website address is provided below. The company logo is attached. We provide specialized permafrost services to the mining, transportation, and oil & gas industries. The card should be prepared for:
Matthias Korhonen, PhD.
Coastal Tundrabridge Advisory
PO Box 418259
Quillwater, Alaska 99642
Direct: +1-907-555-0143
Email: mkorhonen@tundrabridgeadvisory.example
Website: www.coastaltundrabridgeadvisory.example

```html
<!DOCTYPE html>
<html lang="en">
<head>
<meta charset="utf-8">
<title>Coastal Tundrabridge Advisory — Business Card</title>
<link href="https://fonts.googleapis.com/css2?family=Montserrat:wght@400;500;700;800&display=swap" rel="stylesheet">
<style>
  :root {
    --backdrop: #2a2b2e;
    --card-dark: #131820;
    --card-dark-edge: #1d2530;
    --card-light: #ffffff;
    --ink: #15181d;
    --ink-soft: #2b2f36;
    --silver: #e9edf2;
    --silver-dim: #8e98a6;
  }
  * { box-sizing: border-box; margin: 0; padding: 0; }
  html, body { width: 1200px; height: 900px; overflow: hidden; }
  body {
    background: var(--backdrop);
    font-family: "Montserrat", sans-serif;
    position: relative;
  }
  .card {
    position: absolute;
    width: 620px;
    height: 354px;
    border-radius: 18px;
    overflow: hidden;
    box-shadow: 0 18px 40px rgba(0,0,0,0.45);
  }
  /* Back side */
  .card--back {
    left: 150px; top: 70px;
    background: var(--card-dark);
  }
  .card--back .pattern-field {
    position: absolute; inset: 0;
    background: linear-gradient(125deg, #3a4350 0%, #1e252f 30%, #141a22 55%, #0f141b 100%);
  }
  .card--back .brand-mark {
    position: absolute;
    left: 330px; top: 222px;
    display: flex; align-items: center; gap: 10px;
    background: var(--card-dark);
    padding: 10px 14px;
    border-radius: 4px;
  }
  .brand-mark__dot {
    width: 12px; height: 12px; border-radius: 50%;
    background: var(--silver);
  }
  .brand-mark__name {
    color: var(--silver);
    font-weight: 700;
    font-size: 15px;
    letter-spacing: 0.04em;
    text-transform: uppercase;
    line-height: 1.25;
  }
  /* Front side */
  .card--front {
    left: 430px; top: 476px;
    background: var(--card-light);
  }
  .card--front .side-band {
    position: absolute; top: 0; right: 0; bottom: 0;
    width: 150px;
    background: linear-gradient(180deg, var(--card-dark-edge) 0%, var(--card-dark) 100%);
  }
  .side-band__name {
    position: absolute;
    left: 50%; top: 50%;
    transform: translate(-50%, -50%) rotate(90deg);
    white-space: nowrap;
    color: var(--silver);
    font-weight: 700;
    font-size: 14px;
    letter-spacing: 0.12em;
    text-transform: uppercase;
  }
  .holder {
    position: absolute; left: 42px; top: 62px;
    color: var(--ink);
  }
  .holder__name { font-weight: 800; font-size: 21px; }
  .holder__title { font-size: 13px; margin-top: 4px; margin-left: 14px; color: var(--ink-soft); }
  .contact {
    position: absolute; left: 56px; top: 196px;
    color: var(--ink-soft);
    font-size: 12.5px;
    line-height: 1.45;
  }
  .contact__address { margin-left: 0; margin-bottom: 14px; }
  .contact__list { list-style: none; }
  .contact__list li {
    display: flex; align-items: center; gap: 12px;
    margin-bottom: 5px;
  }
  .contact__list svg { width: 13px; height: 13px; flex: none; }
</style>
</head>
<body>

<section class="card card--back" aria-label="Card back">
  <div class="pattern-field" role="img" aria-label="Repeating company name pattern in glossy dark silver"></div>
  <div class="brand-mark">
    <span class="brand-mark__dot"></span>
    <span class="brand-mark__name">Coastal Tundrabridge<br>Advisory</span>
  </div>
</section>

<section class="card card--front" aria-label="Card front">
  <div class="holder">
    <p class="holder__name">Matthias Korhonen, PhD.</p>
    <p class="holder__title">Managing Director</p>
  </div>

  <div class="contact">
    <p class="contact__address">PO Box 418259<br>Quillwater, Alaska 99642</p>
    <ul class="contact__list">
      <li>
        <svg viewBox="0 0 16 16" aria-hidden="true"><path d="M3.5 1.5l2.5 0 1 3.5-1.7 1.2a9 9 0 0 0 4.5 4.5L11 9l3.5 1v2.5c0 1-1 2-2 2A11 11 0 0 1 1.5 3.5c0-1 1-2 2-2z" fill="#15181d"/></svg>
        <span>+1-907-555-0143</span>
      </li>
      <li>
        <svg viewBox="0 0 16 16" aria-hidden="true"><rect x="1" y="3" width="14" height="10" rx="1" fill="#15181d"/><path d="M1.5 3.5L8 9l6.5-5.5" stroke="#fff" stroke-width="1.3" fill="none"/></svg>
        <span>mkorhonen@tundrabridgeadvisory.example</span>
      </li>
      <li>
        <svg viewBox="0 0 16 16" aria-hidden="true"><circle cx="8" cy="8" r="6.5" fill="#15181d"/><path d="M1.5 8h13M8 1.5c2.5 2.5 2.5 10.5 0 13M8 1.5c-2.5 2.5-2.5 10.5 0 13" stroke="#fff" stroke-width="1" fill="none"/></svg>
        <span>www.coastaltundrabridgeadvisory.example</span>
      </li>
    </ul>
  </div>

  <div class="side-band">
    <span class="side-band__name">Coastal Tundrabridge Advisory</span>
  </div>
</section>

</body>
</html>
```